Construction company business card

One side to be the logo with the company name, The other side I would like: (Tomas verbick) Project manager 41 barrow crescent hallam 52917306224783(03) 9703 2428Info@gudeljgroup.comAnd then maybe a couple dot points saying what we do:Construction (commercial & industrial) Civil construction

Anything else please contact me!
Maybe curved st one edge of the card

Target Market(s)

Older clientele

Industry/Entity Type

Construction Company

Contact Information for Business Card

Read above

Colors
3277b5
1b1b1b
9d9d9d

Requirements
Must have
• Use my logo on one side
Nice to have
• Read above
Should not have
• Read above

```html
<!DOCTYPE html>
<html lang="en">
<head>
<meta charset="utf-8">
<title>Ardent Build Group – Business Card</title>
<link href="https://fonts.googleapis.com/css2?family=Roboto:wght@400;500;700;900&display=swap" rel="stylesheet">
<style>
  :root {
    --blue: #3277b5;
    --blue-deep: #2f5f93;
    --ink: #1b1b1b;
    --text: #2b2b2b;
    --grey: #9d9d9d;
    --icon: #666666;
    --card: #f2f2f2;
    --card-edge: #e6e6e6;
    --backdrop: #b5b5b5;
  }
  * { box-sizing: border-box; margin: 0; padding: 0; }
  html, body {
    width: 1200px; height: 576px; overflow: hidden;
    background: var(--backdrop);
    font-family: "Roboto", Arial, sans-serif;
    color: var(--ink);
  }
  .stage { position: relative; width: 1200px; height: 576px; }

  .card {
    position: absolute;
    width: 484px; height: 294px;
    background: linear-gradient(160deg, #f7f7f7 0%, var(--card) 55%, var(--card-edge) 100%);
    border-radius: 4px 26px 4px 26px;
    box-shadow: 0 3px 6px rgba(0,0,0,0.25);
    overflow: hidden;
  }
  .card--front { left: 82px; top: 138px; }
  .card--back  { left: 602px; top: 138px; }

  /* Front */
  .front-mark {
    position: absolute; left: 192px; top: 36px;
    width: 100px; height: 100px; border-radius: 50%;
    background: var(--blue-deep);
  }
  .front-name {
    position: absolute; left: 0; right: 0; top: 166px;
    text-align: center;
    font-size: 30px; font-weight: 900; letter-spacing: 1px;
    text-transform: uppercase; color: var(--blue-deep);
  }
  .front-web {
    position: absolute; left: 0; right: 0; top: 233px;
    display: flex; justify-content: center; align-items: center; gap: 10px;
    font-size: 12.5px; color: var(--text);
  }
  .front-web .rule { width: 36px; height: 2px; background: var(--icon); border-radius: 2px; }
  .front-services {
    position: absolute; left: 0; right: 0; top: 256px;
    text-align: center; font-size: 13px; color: var(--text);
  }
  .front-band {
    position: absolute; left: 0; right: 0; bottom: 0; height: 11px;
    display: flex;
  }
  .front-band .band-grey { flex: 1; background: var(--grey); }
  .front-band .band-blue { flex: 1; background: var(--blue-deep); }

  /* Back */
  .back-mark { position: absolute; left: 0; top: 0; }
  .back-info { position: absolute; left: 246px; top: 34px; }
  .back-company {
    font-size: 21px; font-weight: 900; letter-spacing: 0.5px;
    text-transform: uppercase; color: var(--blue-deep);
    line-height: 1;
  }
  .back-person { margin-top: 38px; }
  .person-name { font-size: 17px; font-weight: 700; color: var(--blue-deep); }
  .person-role { font-size: 12.5px; color: var(--text); margin-top: 3px; }
  .contact-list { list-style: none; margin-top: 18px; font-size: 12.5px; color: var(--text); }
  .contact-list li { display: flex; align-items: center; height: 19.5px; }
  .contact-list svg { width: 10px; height: 10px; margin-right: 14px; fill: var(--icon); flex: none; }
  .back-address { font-size: 12.5px; color: var(--text); height: 19.5px; line-height: 19.5px; }
  .back-services {
    margin-top: 8px; font-size: 12px; line-height: 17px; color: var(--blue-deep);
  }
</style>
</head>
<body>
<main class="stage">

  <section class="card card--front" aria-label="Card front">
    <div class="front-mark" aria-hidden="true"></div>
    <h1 class="front-name">Ardent Build Group</h1>
    <p class="front-web"><span class="rule"></span>www.ardentbuildgroup.com<span class="rule"></span></p>
    <p class="front-services">Construction (Commercial &amp; Industrial) Civil Construction</p>
    <div class="front-band"><span class="band-grey"></span><span class="band-blue"></span></div>
  </section>

  <section class="card card--back" aria-label="Card back">
    <svg class="back-mark" width="240" height="294" viewBox="0 0 240 294" aria-hidden="true">
      <circle cx="100" cy="150" r="112" fill="none" stroke="var(--grey)" stroke-width="26"/>
    </svg>
    <div class="back-info">
      <h2 class="back-company">Ardent Build Group</h2>
      <div class="back-person">
        <p class="person-name">Tomas Verbick</p>
        <p class="person-role">Project Manager</p>
      </div>
      <ul class="contact-list">
        <li><svg viewBox="0 0 10 10"><path d="M1 3 Q5 0 9 3 L8 4.5 L6.5 3.8 L6.5 3 Q5 2.5 3.5 3 L3.5 3.8 L2 4.5 Z M2 5.5 H8 L9 9 H1 Z"/></svg>(73) 0622 4783</li>
        <li><svg viewBox="0 0 10 10"><path d="M0 2 H10 V8 H0 Z M0.8 2.6 L5 5.6 L9.2 2.6 V3.4 L5 6.4 L0.8 3.4 Z" fill-rule="evenodd"/></svg>(03) 9418 6573</li>
        <li><svg viewBox="0 0 10 10"><circle cx="5" cy="5" r="4.3" fill="none" stroke="#666" stroke-width="0.9"/><path d="M0.7 5 H9.3 M5 0.7 V9.3" stroke="#666" stroke-width="0.8"/></svg>Info@verbickgroup.com</li>
      </ul>
      <p class="back-address">41 Barrow Crescent Kelwood 5291</p>
      <p class="back-services">Construction (Commercial<br>&amp; Industrial) Civil Construction</p>
    </div>
  </section>

</main>
</body>
</html>
```